BUSINESS CARD - HALLORAN FIELD SERVICES

I would like to create a business card for my fertilizer spreading business. I would like to incorporate my existing logo and also a description of the services offered. The business card will be given to farmers so must be kept simple but effective. It will also be left in stores so much also be eye catching in order to stand out from other cards.

Target Market(s)

FARMERS

Requirements
Must have
• FRONT OF CARD = EXISTING LOGO + "CUSTOMISED SPREADING" below the logo

REAR Of CARD = SERVICES OFFERED AND CONTACT DETAILS

- Bulk fertilizer including Lime, Gypsum, Manure & Compost
- Granular fertilizer including Single Super, Urea, Gran-am, & Custom Blends
- Modern equipment - Autosteer & Variable Rate Capable
- Friendly & Reliable Service
- Contact Gus: 0417 552 308
Nice to have
• utilize same color scheme as existing logo

```html
<!DOCTYPE html>
<html lang="en">
<head>
<meta charset="utf-8">
<title>Halloran Field Services – Business Card</title>
<link href="https://fonts.googleapis.com/css2?family=Lato:wght@400;700&display=swap" rel="stylesheet">
<style>
  :root {
    --page: #efeeef;
    --card-white: #ffffff;
    --orange: #f7941e;
    --charcoal: #58585a;
    --text-grey: #555557;
  }
  * { margin: 0; padding: 0; box-sizing: border-box; }
  html, body { width: 1146px; height: 1200px; overflow: hidden; }
  body { background: var(--page); font-family: "Lato", sans-serif; position: relative; }

  .card {
    position: absolute;
    left: 189px;
    width: 765px;
    height: 440px;
    border-radius: 30px;
    overflow: hidden;
  }
  .card--front { top: 153px; background: var(--card-white); }
  .card--back  { top: 636px; background: var(--orange); color: #fff; }

  /* brand block */
  .brand { position: absolute; text-align: center; }
  .brand__mark { display: block; margin: 0 auto 14px; border-radius: 50%; }
  .brand__name { font-weight: 700; font-size: 33px; line-height: 1.05; letter-spacing: -0.5px; }

  .card--front .brand { left: 50px; top: 120px; width: 316px; color: var(--charcoal); }
  .card--front .brand__mark { width: 110px; height: 110px; background: var(--charcoal); }

  .card--back .brand { left: 0; top: 60px; width: 765px; color: #fff; }
  .card--back .brand__mark { width: 120px; height: 120px; background: #fff; }
  .card--back .brand__name { font-size: 36px; }

  /* contact column */
  .divider { position: absolute; left: 382px; top: 126px; width: 1.5px; height: 188px; background: var(--charcoal); }
  .contact { position: absolute; left: 399px; top: 118px; color: var(--text-grey); }
  .contact__name { color: var(--orange); font-weight: 700; font-size: 27px; line-height: 1.1; }
  .contact__role { font-size: 18px; margin-top: 2px; }
  .contact__address { font-size: 18px; line-height: 1.3; margin-top: 9px; }
  .contact__list { list-style: none; margin-top: 9px; }
  .contact__list li { display: flex; align-items: center; font-size: 18px; line-height: 22px; }
  .contact__list svg { width: 14px; height: 14px; margin-right: 9px; fill: var(--orange); flex: none; }

  /* bottom band */
  .band { position: absolute; left: 0; bottom: 0; width: 765px; height: 18px; }

  /* services list */
  .services { position: absolute; left: 0; top: 300px; width: 765px; list-style: none; text-align: center; }
  .services li { font-size: 17px; font-weight: 700; line-height: 23.5px; }
</style>
</head>
<body>

<section class="card card--front">
  <div class="brand">
    <span class="brand__mark"></span>
    <div class="brand__name">Halloran Field Services</div>
  </div>

  <div class="divider"></div>

  <div class="contact">
    <div class="contact__name">Darren Whitcombe</div>
    <div class="contact__role">Co-founder</div>
    <div class="contact__address">48 Mill Road, Dunmore<br>3315</div>
    <ul class="contact__list">
      <li><svg viewBox="0 0 16 16"><path d="M3 1l3 3-1.5 2a9 9 0 0 0 5.5 5.5L12 10l3 3-2 2C7 15 1 9 1 3z"/></svg>03 5571 2846</li>
      <li><svg viewBox="0 0 16 16"><path d="M1 6c0-2 3-3 7-3s7 1 7 3v1h-3V5.5H4V7H1zM3 8h10l1 6H2zm5 1.5a2 2 0 1 0 0 4 2 2 0 0 0 0-4z"/></svg>0417 552 308</li>
      <li><svg viewBox="0 0 16 16"><path d="M1 3h14v10H1zm1.5 1.5L8 9l5.5-4.5v-.1h-11z"/></svg>hello@halloranfield.net</li>
      <li><svg viewBox="0 0 16 16"><path d="M8 1a7 7 0 1 0 0 14A7 7 0 0 0 8 1zm0 2c.8 1 1.3 2.5 1.4 4H6.6C6.7 5.5 7.2 4 8 3zM3.1 9h2.4c.1 1.5.5 2.8 1.1 3.8A5 5 0 0 1 3.1 9zm7.4 0h2.4a5 5 0 0 1-3.5 3.8c.6-1 1-2.3 1.1-3.8z"/></svg>www.halloranfield.net</li>
    </ul>
  </div>

  <svg class="band" viewBox="0 0 765 18" preserveAspectRatio="none" aria-hidden="true">
    <rect x="0" y="0" width="765" height="18" fill="var(--orange)"/>
    <polygon points="0,0 400,0 366,18 0,18" fill="var(--charcoal)"/>
    <polygon points="400,0 404,0 370,18 366,18" fill="#ffffff"/>
  </svg>
</section>

<section class="card card--back">
  <div class="brand">
    <span class="brand__mark"></span>
    <div class="brand__name">Halloran Field Services</div>
  </div>

  <ul class="services">
    <li>Modern equipment</li>
    <li>Friendly &amp; Reliable Services</li>
    <li>Bulk fertilizer including Lime, Gypsum, Manure &amp; Composts</li>
    <li>Granular fertilizer including Single Super, Urea, Gran-am, &amp; Custom Blends</li>
  </ul>
</section>

</body>
</html>
```